Anzeigenerstellung für ein Hochglanzmagazin
Zielgruppe
Männer und Frauen, junge Familien bis hin zum Senior.
Verkauf von hochwertigen Immobilien in Spanien.
Aufgabenstellung
Wir benötigen ein schönes und frisches Anzeigendesign, gerne im Magazinstil mit einem Luxus-Touch. Es handelt sich hierbei um eine Imageanzeige, nicht um eine spezifische Immobilienanzeige. Wir sind eine skandinavische Agentur für Luxus-Immobilien auf Mallorca. Das Design sollte dementsprechend edel aber dennoch schlicht gestaltet sein!

```html
<!DOCTYPE html>
<html lang="en">
<head>
<meta charset="utf-8">
<title>Norvik Homes – Luxury Real Estates</title>
<link rel="stylesheet" href="https://fonts.googleapis.com/css2?family=Josefin+Sans:wght@300;400&display=swap">
<style>
  :root {
    --navy: #1c3764;
    --sky-top: #3f86d4;
    --sky-low: #a9cbe9;
    --sea: #1f5391;
    --terrace: #cfccc5;
    --terrace-low: #bbb8b1;
    --band: rgba(255, 255, 255, 0.58);
  }
  * { margin: 0; padding: 0; box-sizing: border-box; }
  html, body { width: 928px; height: 1200px; overflow: hidden; background: #fff; }
  .ad {
    position: relative;
    width: 928px;
    height: 1200px;
    overflow: hidden;
    font-family: "Josefin Sans", "Helvetica Neue", Arial, sans-serif;
    color: var(--navy);
  }
  .hero-photo {
    position: absolute;
    inset: 0;
    background: linear-gradient(180deg,
      var(--sky-top) 0%,
      var(--sky-low) 48%,
      var(--sea) 52%,
      var(--sea) 60%,
      var(--terrace) 63%,
      var(--terrace-low) 100%);
  }
  .light-band {
    position: absolute;
    top: 0;
    left: 504px;
    width: 302px;
    height: 1200px;
    background: var(--band);
  }
  .headline {
    position: absolute;
    top: 126px;
    right: 139px;
    text-align: right;
    font-weight: 400;
    font-size: 50px;
    line-height: 73px;
    letter-spacing: -1px;
  }
  .brand {
    position: absolute;
    top: 1026px;
    right: 139px;
    font-size: 32px;
    font-weight: 400;
    letter-spacing: 0;
  }
  .contact {
    position: absolute;
    top: 1078px;
    right: 139px;
    text-align: right;
    font-style: normal;
    font-size: 12px;
    line-height: 25px;
    font-weight: 300;
  }
</style>
</head>
<body>
  <main class="ad">
    <div class="hero-photo" role="img" aria-label="Photo of a white Mediterranean villa terrace with a large white vase and a dog lying on the stone floor, blue sky and sea behind"></div>
    <div class="light-band"></div>
    <h1 class="headline">LUXURY<br>REAL<br>ESTATES<br>FOR<br>MALLORCA<br>&amp; IBIZA</h1>
    <div class="brand">Norvik Homes</div>
    <address class="contact">
      C. Mirador 4<br>
      07150 Port Blau, Spain | Tel. 971000123<br>
      info@norvikhomes.com | www.norvikhomes.com
    </address>
  </main>
</body>
</html>
```